Morvane Capital, a private equity fund, needs a brochure

Morvane Capital is a private equity fund dedicated to the development of budget hotels in France (reasonably priced hotel rooms).
Our customers are French private and high-income investors.

The brochure should communicate :
- seriousness and expertise
- trust, confidence and security
- financial product and profitability

The title is : Investissez dans l'hôtellerie économique et l'immobilier

Brochure size :
3 pages A4
Open size : 63 x 29,7 cm
Closed size : 21 x 29,7 cm

Our competitors :
Trelisse http://trelisse-immo-horizon.example/
789 Parcours http://www.789parcours.example/
GLD Capital http://www.gldam.example/
Soltane capital http://www.soltanecapital.example/
Barostel http://www.barostel.example/

Target Market(s)

Private investors, high-income ; Institutional investors ; Target customers are French private investors with high revenue.

Industry/Entity Type

Financial

Requirements
Must have
• - Brochure must respect our identity (you can see our logo) and use its colors and typo (and/or same typo style)
- You must use pictures on each interior pages (pictures of projetc and hotels)

```html
<!DOCTYPE html>
<html lang="fr">
<head>
<meta charset="utf-8">
<title>Morvane Capital – Typologie des frais</title>
<link rel="stylesheet" href="https://fonts.googleapis.com/css2?family=Source+Sans+3:wght@400;600;700&display=swap">
<style>
:root{
  --stage:#2a3236;
  --page:#dcdfe1;
  --band:#e8e9ea;
  --head:#eceeef;
  --red:#c8202f;
  --ink:#1f1f1f;
  --text:#3a3a3a;
  --rule:#7d8184;
  --photo-lobby:#9a5a4a;
  --photo-facade:#8a7a66;
  --photo-sign:#6b4a2c;
  --photo-man:#3a3b40;
}
*{box-sizing:border-box;margin:0;padding:0}
html,body{width:900px;height:1200px;overflow:hidden}
body{background:var(--stage);font-family:"Source Sans 3",Arial,sans-serif;color:var(--text);position:relative}
.page{position:absolute;left:50px;top:37px;width:805px;height:1138px;background:var(--page);overflow:hidden}
.abs{position:absolute}
.photo-band{left:38px;top:11px;width:767px;height:214px;background:var(--band)}
.photo{top:25px;height:190px}
.photo--lobby{left:48px;width:245px;background:linear-gradient(135deg,#e9e6e2 0%,var(--photo-lobby) 55%,#5e3a2e 100%)}
.photo--facade{left:311px;width:245px;background:linear-gradient(180deg,#9fb9d3 0%,#c9b49a 45%,var(--photo-facade) 100%)}
.photo--sign{left:574px;width:231px;background:linear-gradient(160deg,#e0a550 0%,var(--photo-sign) 60%,#2c1e14 100%)}

.fees-title{left:45px;top:239px;color:var(--red);font-weight:700;font-size:15px}
.fees{left:45px;width:368px;font-size:11.5px;color:var(--ink);line-height:1.2}
.fees .row{display:flex;border-bottom:1px solid var(--rule);padding:3px 0 4px 1px}
.fees .row span:nth-child(1){width:146px}
.fees .row span:nth-child(2){width:146px}
.fees .row span:nth-child(3){width:76px}
.fees .row.head{background:var(--head);color:var(--red);font-weight:700;border-bottom:2px solid var(--rule);align-items:flex-end;padding:2px 0 3px 1px;height:33px}
.fees .row.total{border-bottom:none;font-weight:700}
.fees--once{top:263px}
.fees--yearly{top:415px}

.notes{left:450px;top:313px;width:302px;font-size:9.6px;line-height:1.32;color:var(--ink)}
.notes p{margin-bottom:9px}

.warning{left:38px;top:625px;width:722px;height:218px;border:1px solid var(--rule);padding:13px 14px 0 31px;font-size:10.6px;line-height:1.6;color:var(--text)}
.warning p{margin-bottom:14px}
.warning strong{color:var(--ink)}
.warning .bullet{position:absolute;left:14px;top:19px;width:8px;height:8px;background:var(--red)}

.brand{left:0;top:860px;width:805px;text-align:center}
.brand-name{display:inline-flex;align-items:center;gap:9px;font-size:30px;font-weight:600;color:var(--ink);letter-spacing:.04em}
.brand-name i{width:14px;height:14px;background:var(--red);display:inline-block}
.brand-address{font-weight:700;font-size:12.5px;color:var(--ink);line-height:1.65;margin-top:6px}

.person{background:linear-gradient(180deg,#c9ccce 0%,#b7b0a8 35%,var(--photo-man) 100%)}
.person--left{left:0;top:933px;width:155px;height:205px}
.person--right{left:680px;top:928px;width:125px;height:210px}
.rule{height:1px;background:var(--rule);left:148px;width:527px}
.contact{top:959px;font-size:12.5px;line-height:1.35;color:var(--ink)}
.contact h3{color:var(--red);font-size:14px;font-weight:700}
.contact .name{font-weight:700}
.contact--left{left:155px}
.contact--right{left:537px}
.legal{left:0;top:1042px;width:805px;text-align:center;font-size:11px;line-height:1.45;color:var(--text)}
</style>
</head>
<body>
<main class="page">
  <div class="abs photo-band"></div>
  <div class="abs photo photo--lobby" role="img" aria-label="Photo d'une réception d'hôtel moderne aux murs rouges"></div>
  <div class="abs photo photo--facade" role="img" aria-label="Photo de la façade d'un hôtel économique avec terrasse"></div>
  <div class="abs photo photo--sign" role="img" aria-label="Photo d'une enseigne Hotel sur un balcon en fer forgé de nuit"></div>

  <h2 class="abs fees-title">Typologie des frais</h2>

  <div class="abs fees fees--once">
    <div class="row head"><span>Frais ponctuels<br>(années de souscription)</span><span>Taux</span><span>Assiette</span></div>
    <div class="row"><span>Droits d’entrée et/ou sortie</span><span>0%</span><span></span></div>
    <div class="row"><span>Frais de constitution (1)</span><span>1,00% HT maximum</span><span>Montant des souscriptions</span></div>
    <div class="row"><span>Frais de communication (2)</span><span>2,50% HT maximum</span><span>Montant des souscriptions</span></div>
    <div class="row total"><span>Totaux</span><span>3,50% HT maximum</span><span></span></div>
  </div>

  <div class="abs fees fees--yearly">
    <div class="row head"><span>Frais annuels</span><span>Taux</span><span>Assiette</span></div>
    <div class="row"><span>Frais récurrents de gestion et de fonctionnement (3)</span><span>30 000 € HT minimum<br>1,30% HT maximum</span><span>Actif net</span></div>
    <div class="row"><span>Frais liés aux investissements (4)</span><span>0,50% HT maximum</span><span>Actif net</span></div>
    <div class="row"><span>Frais d’abonnement de conseil juridique et fiscal</span><span>0,10% HT maximum</span><span>Actif net</span></div>
    <div class="row"><span>Frais relatifs à l’information des actionnaires (5)</span><span>1,00% HT maximum</span><span>Actif net</span></div>
    <div class="row total"><span>Totaux</span><span>2,90% HT maximum</span><span></span></div>
  </div>

  <div class="abs notes">
    <p>(1) Les frais de constitution de la société correspondent aux frais et charges supportés par la société pour sa création (frais d’avocat, de parution, de conseils etc.)</p>
    <p>(2) Les frais de communication correspondent à la promotion de la société (frais marketing, frais de publicité, etc.)</p>
    <p>(3) Les frais récurrents de gestion et de fonctionnement comprennent notamment la rémunération de la Présidence (gestionnaire, dont la rémunération est variable et dégressive), ils intègrent également les frais de comptabilité et des commissaires aux comptes etc.</p>
    <p>(4) Les frais de fonctionnement liés aux investissements sont tous les frais liés aux activités d’investissement de la société. Ces frais recouvrent les frais et honoraires d’audit, d’études et de conseils, droits d’enregistrement relatifs à l’acquisition, la cession de titres et au suivi des participations, etc.</p>
    <p>(5) Les frais relatifs à l’information des actionnaires sont occasionnés pour le reporting de l’information semestrielle des actionnaires de la société. Ils sont attribués à la présidence qui pourra l’affecter, le cas échéants, à des sous-traitants. Ils représentent 1% HT maximum de l’actif net sans toutefois dépasser le plafond de 5.000 € HT par actionnaire.</p>
  </div>

  <section class="abs warning">
    <span class="bullet"></span>
    <p><strong>Avertissement important:</strong> la présente notice d’information relative à la souscription à l’augmentation de capital de Morvane Capital, SAS à capital variable, ne constitue pas une offre au public de titres financiers au sens de l’article L. 411-1 du Code monétaire et financier (CMF). L’investissement dans Morvane capital est réservé aux investisseurs qui effectuent une souscription minimale de 100.000 euros conformément aux dispositions du paragraphe 2° du I de l’article L. 422-2 du CMF. L’opération présentée ne donne donc pas lieu à un prospectus soumis au visa de l’Autorité des Marchés Financiers.</p>
    <p>Les personnes ou entités mentionnées au 2° du II de l’article L. 411-2 du CMF ne peuvent participer à cette offre que pour compte propre dans les conditions fixées par les articles D. 411-1, D. 411-2,<br>D. 734-1, D. 744-1, D. 754-1 et D. 764-1 du CMF.</p>
    <p>La diffusion, directe ou indirecte, dans le public des instruments financiers ainsi acquis ne peut être réalisée que dans les conditions prévues aux articles L. 411-1, L. 411-2, L. 412-1 et L. 621-8 à L. 621-8-3 du CMF.</p>
  </section>

  <div class="abs brand">
    <div class="brand-name"><i></i>Morvane Capital</div>
    <div class="brand-address">42 rue des Tilleuls 75008 – Paris<br>Téléphone: 01 40 00 12 34 – Fax: 01 40 00 56 78</div>
  </div>

  <div class="abs person person--left" role="img" aria-label="Portrait du responsable investisseurs institutionnels"></div>
  <div class="abs person person--right" role="img" aria-label="Portrait du responsable relations partenaires"></div>

  <div class="abs rule" style="top:952px"></div>
  <div class="abs contact contact--left">
    <h3>Investisseurs institutionnels</h3>
    <div class="name">Étienne-Marc Dravalle</div>
    <div>06 00 11 22 33</div>
    <div>emd@groupe-morvane.example</div>
  </div>
  <div class="abs contact contact--right">
    <h3>Relations partenaires</h3>
    <div class="name">Olivier de Saint-Arven</div>
    <div>06 00 44 55 66</div>
    <div>osa@groupe-morvane.example</div>
  </div>
  <div class="abs rule" style="top:1035px"></div>

  <div class="abs legal">
    Morvane Capital, société par actions simplifiée à capital variable<br>
    Siège social: Immeuble Alizé, 3 zone de Belcourt, 97200 Port-Lestrie<br>
    000 123 456 RCS Port-Lestrie
  </div>
</main>
</body>
</html>
```